sydney wedding photography business needs a business card design

we need a business card design for a sydney based wedding photography and videography business. our business name is :golden hour studio and film. our target clients are 24-35 yrs female. our style is candid, organic, natural, dynamic. we are a team of young photographers and videographers, and help brides to create memories that they will cherish for the rest of their lives. the logo will be provided. we want an elegant design that reflects our style, and also want to give a great impression to our clients that we are one of the best studios in sydney and our brand means quality and premium service.

Target Market(s)

bride to be, 24-35 years old, living in sydney and surrunding areas

Industry/Entity Type

Wedding Photography

Contact Information for Business Card

address: 57 tarrant street, glenmore nsw 2047
mobile: 0431872259
phone: (02) 9163 2408
info@tidewillowstudio.net.au
www.tidewillowstudio.net.au
facebook:tidewillowweddings
instagram:tidewillowweddings

Font styles to use
Serif
Sans Serif

Requirements
Nice to have
• maybe add my slogan"memories beyond eternity" if the layout looks good
Should not have
• no black color, not good idea for wedding biz card

```html
<!DOCTYPE html>
<html lang="en">
<head>
<meta charset="utf-8">
<title>Golden Hour Studio and Film – Business Card</title>
<link rel="stylesheet" href="https://fonts.googleapis.com/css2?family=Jost:wght@400;500;600&display=swap">
<style>
  :root {
    --backdrop: #464646;
    --card-front: #3a2e25;
    --card-front-edge: #31271f;
    --gold: #d9a514;
    --gold-light: #e2b21c;
    --gold-deep: #b8860d;
    --ink: #2a2118;
    --text-light: #efe6da;
  }
  * { margin: 0; padding: 0; box-sizing: border-box; }
  html, body {
    width: 1200px; height: 750px; overflow: hidden;
    background: var(--backdrop);
    font-family: "Jost", Arial, sans-serif;
  }
  .canvas { position: relative; width: 1200px; height: 750px; }
  .card {
    position: absolute; top: 229px;
    width: 461px; height: 261px;
  }
  .card--front {
    left: 124px;
    background: radial-gradient(ellipse at 40% 40%, var(--card-front) 0%, var(--card-front-edge) 100%);
  }
  .card--back {
    left: 618px;
    background: radial-gradient(ellipse at 50% 35%, var(--gold-light) 0%, var(--gold) 45%, var(--gold-deep) 100%);
  }
  .ring-art {
    position: absolute; left: 326px; top: 18px;
    width: 105px; height: 120px;
  }
  .holder { position: absolute; left: 22px; top: 134px; }
  .holder__name {
    color: var(--gold); font-size: 20px; font-weight: 400;
    letter-spacing: 0.5px; text-transform: uppercase; line-height: 1;
  }
  .holder__role {
    color: var(--text-light); font-size: 12px; margin-top: 7px; line-height: 1;
    text-transform: uppercase; letter-spacing: 0.3px;
  }
  .divider {
    position: absolute; left: 22px; top: 182px;
    width: 410px; height: 1px; background: var(--gold);
  }
  .contacts {
    position: absolute; left: 22px; top: 190px;
    color: var(--text-light); font-size: 13px; line-height: 16.5px;
    list-style: none;
  }
  .contacts__label { color: var(--gold); margin-right: 4px; }
  .contacts__sep { color: var(--gold); margin: 0 4px 0 6px; }
  .brand {
    position: absolute; left: 0; right: 0; top: 96px;
    text-align: center; color: var(--ink);
  }
  .brand__name { font-size: 40px; line-height: 1; font-weight: 600; letter-spacing: 0.5px; }
  .brand__sub {
    font-size: 12px; font-weight: 600; letter-spacing: 7px; margin-top: 10px; line-height: 1;
    text-transform: uppercase;
  }
  .social {
    position: absolute; left: 0; right: 0; top: 214px;
    display: flex; justify-content: center; align-items: center; gap: 6px;
    color: var(--ink); font-size: 12px; line-height: 1; text-transform: uppercase; letter-spacing: 0.3px;
  }
  .social__dot { width: 13px; height: 13px; border-radius: 50%; background: var(--ink); }
</style>
</head>
<body>
<main class="canvas">
  <section class="card card--front">
    <svg class="ring-art" role="img" aria-label="Gold engagement ring with diamond illustration" viewBox="0 0 105 120">
      <defs>
        <linearGradient id="ringFill" x1="0" y1="0" x2="0" y2="1">
          <stop offset="0" stop-color="#e8b820"/>
          <stop offset="1" stop-color="#b88a0e"/>
        </linearGradient>
      </defs>
      <rect x="0" y="0" width="105" height="120" rx="14" fill="url(#ringFill)"/>
    </svg>
    <div class="holder">
      <h1 class="holder__name">Mia Hartley</h1>
      <p class="holder__role">Photographer</p>
    </div>
    <div class="divider"></div>
    <ul class="contacts">
      <li><span class="contacts__label">P :</span>(02) 9163 2408<span class="contacts__sep">M :</span>(04) 3187 2259</li>
      <li><span class="contacts__label">E :</span>info@tidewillowstudio.net.au<span class="contacts__sep">W :</span>tidewillowstudio.net.au</li>
      <li><span class="contacts__label">A :</span>57 tarrant street, glenmore nsw 2047</li>
    </ul>
  </section>

  <section class="card card--back">
    <div class="brand">
      <p class="brand__name">Golden Hour</p>
      <p class="brand__sub">Studio and Film</p>
    </div>
    <div class="social">
      <span class="social__dot"></span>
      <span>tidewillowweddings</span>
    </div>
  </section>
</main>
</body>
</html>
```